Pearlview Family Dentistry
Logo For Dental Office
Professional
Noreen Halvik
DMD
2785 Marlow Lane Suite 204 Virginia Beach, VA 23817
pearlview482@quillpost.net
pearlviewfamilydentistry-example.net
I would like shades of blue in my logo
Appointment card on the back
sameed-shafi sameed-shafi
Can you give me an existing copy of your logo.
deadbouy deadbouy
Hello sir, Can you please provide your logo? :)

```html
<!DOCTYPE html>
<html lang="en">
<head>
<meta charset="utf-8">
<title>Pearlview Family Dentistry – Business Card</title>
<link rel="stylesheet" href="https://fonts.googleapis.com/css2?family=Crimson+Text:wght@400&display=swap">
<style>
  :root {
    --page: #ffffff;
    --blue: #1a80c6;
    --blue-light: #3d9ad6;
    --swoosh: #a3a3a3;
    --ink: #2b2b2b;
    --white: #ffffff;
  }
  html, body {
    margin: 0;
    padding: 0;
    overflow: hidden;
    background: var(--page);
  }
  .card {
    position: relative;
    width: 1200px;
    height: 756px;
    background: var(--page);
    font-family: "Crimson Text", Georgia, serif;
    color: var(--ink);
    overflow: hidden;
  }
  .card__header {
    position: absolute;
    left: 0;
    top: 0;
  }
  .brand-name {
    position: absolute;
    left: 250px;
    top: 160px;
    margin: 0;
    font-size: 54px;
    font-weight: 400;
    letter-spacing: 1px;
    color: var(--white);
    line-height: 1;
  }
  .brand-tagline {
    position: absolute;
    left: 760px;
    top: 214px;
    margin: 0;
    font-size: 34px;
    font-weight: 400;
    transform: rotate(-9deg);
    transform-origin: left bottom;
    white-space: nowrap;
  }
  .person {
    position: absolute;
    left: 533px;
    top: 372px;
    margin: 0;
    font-size: 56px;
    font-weight: 400;
    letter-spacing: 1px;
    white-space: nowrap;
  }
  .person__title {
    font-size: 36px;
    letter-spacing: 1px;
  }
  .address {
    position: absolute;
    left: 137px;
    top: 448px;
    margin: 0;
    font-style: normal;
    font-size: 31px;
    line-height: 36px;
  }
  .contact {
    position: absolute;
    left: 596px;
    top: 505px;
    margin: 0;
    font-size: 24px;
    line-height: 38px;
    white-space: nowrap;
  }
  .card__footer-band {
    position: absolute;
    left: 115px;
    top: 595px;
    width: 934px;
    height: 34px;
    background: var(--blue);
  }
</style>
</head>
<body>
  <div class="card">
    <svg class="card__header" width="1200" height="320" viewBox="0 0 1200 320" aria-hidden="true">
      <defs>
        <linearGradient id="header-fill" x1="0" y1="0" x2="0" y2="1">
          <stop offset="0" stop-color="var(--blue-light)"/>
          <stop offset="1" stop-color="var(--blue)"/>
        </linearGradient>
      </defs>
      <path d="M115 96 H1049 V158 C850 250 450 252 115 204 Z" fill="url(#header-fill)"/>
      <path d="M115 212 C450 260 850 258 1049 166" fill="none" stroke="var(--swoosh)" stroke-width="4"/>
    </svg>

    <p class="brand-name">PEARLVIEW</p>
    <p class="brand-tagline">Family Dentistry</p>

    <h1 class="person">Noreen Halvik <span class="person__title">DMD</span></h1>

    <address class="address">
      2785 Marlow Lane<br>
      Suite 204, Virginia Beach,<br>
      VA 23817<br>
      Ph: 757-318-2094
    </address>

    <p class="contact">
      Email: pearlview482@quillpost.net<br>
      www.pearlviewfamilydentistry-example.net
    </p>

    <div class="card__footer-band"></div>
  </div>
</body>
</html>
```